Re-style home page - eye-catching and unique design for social commerce website

We need a new concept design for BrinoKet's home page.
We don't want to make huge changes but creating a more professional and eye-catching style.

We need to look very serious like a professional services company and in the same time to look like a social network for e-commerce.

Our logo is very captive and you can use to creating something of harmonious.

This is a re-style and I'm excepted to see unique and fresh design like Glimmora.

Target Market(s)

e-commerce and social

Industry/Entity Type

Social

Number of Pages Required

1 page

Font styles to use
Serif
Sans Serif

Requirements
Must have
• An eye-catching result.
• Search bar with logo and Login How it works and business
• The slogan with login and signup.
• Footer links.
Nice to have
• I would like to open the home page and see only two clear ways:
• -Consumer
• --Search
• --The slogan
• --Login and Signup
• --How it works
• -Business
• --Go to Business area
• Background: City, Shopping.
Should not have
• Scrollbar style!

```html
<!DOCTYPE html>
<html lang="en">
<head>
<meta charset="utf-8">
<title>BrinoKet – Home</title>
<link rel="stylesheet" href="https://fonts.googleapis.com/css2?family=Roboto:wght@300;400;500;700&display=swap">
<style>
  :root {
    --white: #ffffff;
    --line: rgba(255, 255, 255, 0.75);
    --sky-top: #2f5f92;
    --sky-mid: #4a6f98;
    --street: #b06a3a;
    --street-dark: #3b2a3a;
    --panel-grey: #b9b9bd;
    --bag-pink: #c9457a;
    --bag-tan: #a99478;
    --sleeve: #b0234a;
    --social-blue: #1f3fcf;
    --search-icon: #2f6fe0;
    --field-text: #555a62;
    --accent: #f0822a;
  }
  * { box-sizing: border-box; margin: 0; padding: 0; }
  html, body { width: 1200px; height: 1200px; overflow: hidden; }
  body {
    position: relative;
    font-family: "Roboto", Arial, sans-serif;
    color: var(--white);
  }
  .city-backdrop {
    position: absolute; inset: 0;
    background:
      radial-gradient(ellipse at 80% 85%, rgba(230, 140, 60, 0.55), transparent 55%),
      radial-gradient(ellipse at 15% 80%, rgba(200, 120, 60, 0.45), transparent 50%),
      linear-gradient(180deg, var(--sky-top) 0%, var(--sky-mid) 40%, #6a5f6f 70%, var(--street) 88%, var(--street-dark) 100%);
  }
  .hero-panel {
    position: absolute; left: 190px; top: 140px; width: 820px; height: 818px;
    background:
      linear-gradient(120deg, rgba(185, 185, 189, 0.95) 0%, rgba(185, 185, 189, 0.9) 25%, rgba(201, 69, 122, 0.75) 40%, rgba(169, 148, 120, 0.8) 58%, rgba(120, 110, 100, 0.8) 75%, rgba(176, 35, 74, 0.85) 100%);
  }
  .brand {
    position: absolute; top: 100px; left: 0; width: 1200px;
    display: flex; justify-content: center; align-items: center; gap: 14px;
  }
  .brand-name { font-size: 58px; font-weight: 700; letter-spacing: -1px; }
  .brand-mark { width: 40px; height: 40px; background: var(--accent); }
  .headline {
    position: absolute; top: 190px; width: 1200px; text-align: center;
    font-size: 40px; font-weight: 400;
  }
  .feed-title {
    position: absolute; top: 267px; width: 1200px; text-align: center;
    font-size: 29px; font-weight: 400;
  }
  .feed-grid {
    position: absolute; left: 301px; top: 328px;
    display: grid; grid-template-columns: repeat(3, 190px);
    grid-auto-rows: 50px; column-gap: 13px; row-gap: 15px;
  }
  .feed-grid.last-row { left: 402px; top: 718px; grid-template-columns: repeat(2, 191px); column-gap: 13px; }
  .feed-option {
    border: 1px solid var(--line);
    display: flex; align-items: center; justify-content: center; text-align: center;
    font-size: 14.5px; font-weight: 400; line-height: 1.3; text-transform: uppercase;
  }
  .feed-option.featured { font-weight: 500; font-size: 15px; }
  .slogan {
    position: absolute; top: 798px; width: 1200px; text-align: center;
    font-size: 26px;
  }
  .social-login {
    position: absolute; left: 489px; top: 845px; width: 222px; height: 44px;
    background: var(--social-blue);
    display: flex; align-items: center; gap: 22px; padding-left: 14px;
    font-size: 15px; font-weight: 500;
  }
  .social-login .dot { width: 20px; height: 20px; background: var(--white); opacity: 0.9; }
  .sign-up {
    position: absolute; top: 900px; width: 1202px; text-align: center; font-size: 20px;
  }
  .search-bar {
    position: absolute; left: 424px; top: 1012px; width: 406px; height: 53px;
    background: var(--white); display: flex;
  }
  .search-field {
    flex: 1; display: flex; align-items: center; padding-left: 20px;
    color: var(--field-text); font-size: 17px;
  }
  .search-button {
    width: 58px; border-left: 1px solid #e2e2e2;
    display: flex; align-items: center; justify-content: center;
  }
  .primary-links, .footer-links {
    position: absolute; width: 1200px; text-align: center;
  }
  .primary-links { top: 1091px; font-size: 15px; }
  .footer-links { top: 1123px; font-size: 13.5px; }
  .primary-links span, .footer-links span { margin: 0 4px; }
  .footer-links span { margin: 0 6px; }
</style>
</head>
<body>
  <div class="city-backdrop" role="img" aria-label="Blurred city skyline at dusk with light trails of traffic on a highway"></div>
  <div class="hero-panel" role="img" aria-label="Woman's arm holding a bank card and several colourful shopping bags"></div>

  <header class="brand">
    <span class="brand-name">BrinoKet</span>
    <span class="brand-mark"></span>
  </header>

  <h1 class="headline">Shop directly from your Profile</h1>
  <h2 class="feed-title">SETUP YOUR FEED</h2>

  <div class="feed-grid">
    <div class="feed-option">Active Life</div>
    <div class="feed-option">Arts &amp; Entertainment</div>
    <div class="feed-option">Automotive</div>
    <div class="feed-option">Beauti &amp; Spas</div>
    <div class="feed-option featured">Education</div>
    <div class="feed-option">Event Planning<br>&amp; Services</div>
    <div class="feed-option featured">Financial Services</div>
    <div class="feed-option">Food</div>
    <div class="feed-option">Health &amp; Medical</div>
    <div class="feed-option">Home Servies</div>
    <div class="feed-option">Hotels</div>
    <div class="feed-option">Local Services</div>
    <div class="feed-option">Mass Media</div>
    <div class="feed-option">Nightlife</div>
    <div class="feed-option">Pets</div>
    <div class="feed-option">Professional<br>Services</div>
    <div class="feed-option">Public Services &amp;<br>Goverment</div>
    <div class="feed-option">Real Estate</div>
  </div>
  <div class="feed-grid last-row">
    <div class="feed-option featured">Restaurants</div>
    <div class="feed-option featured">Shopping</div>
  </div>

  <p class="slogan">Save Your Time. Live Better</p>
  <div class="social-login"><span class="dot"></span><span>Login with Friendlink</span></div>
  <p class="sign-up">Sign Up</p>

  <div class="search-bar">
    <div class="search-field">Search here...</div>
    <div class="search-button">
      <svg width="28" height="28" viewBox="0 0 28 28" aria-hidden="true">
        <circle cx="11.5" cy="11.5" r="8.5" fill="none" stroke="var(--search-icon)" stroke-width="3"/>
        <line x1="18" y1="18" x2="25.5" y2="25.5" stroke="var(--search-icon)" stroke-width="3.4" stroke-linecap="round"/>
      </svg>
    </div>
  </div>

  <nav class="primary-links">Login<span>|</span>How it work<span>|</span>Business</nav>
  <nav class="footer-links">About us<span>|</span>Blog<span>|</span>Business Jobs<span>|</span>Privacy<span>|</span>FAQ<span>|</span>Contacts</nav>
</body>
</html>
```